I'm looking for a smart new design for business cards

Industry/Entity Type

Commercial Electrical

Contact Information for Business Card

Logo, name, email, position, website QR

Requirements
Nice to have
• Logo embedded behind the text side

```html
<!DOCTYPE html>
<html lang="en">
<head>
<meta charset="utf-8">
<title>Keystone Volt Electrical – Business Card</title>
<link rel="stylesheet" href="https://fonts.googleapis.com/css2?family=Arimo:wght@400;700&family=Montserrat:wght@800&display=swap">
<style>
  :root {
    --backdrop: #e4e4e4;
    --card-blue: #0e1187;
    --accent-red: #e0003a;
    --paper-white: #ffffff;
    --emboss-blue: #2b34f2;
    --text-white: #ffffff;
  }
  html, body {
    margin: 0;
    width: 1200px;
    height: 1200px;
    overflow: hidden;
    background: var(--backdrop);
  }
  .canvas {
    position: relative;
    width: 1200px;
    height: 1200px;
  }
  .card {
    position: absolute;
    width: 687px;
    height: 393px;
    border-radius: 24px;
    overflow: hidden;
    background: var(--card-blue);
    box-shadow: 0 10px 24px rgba(0,0,0,0.18);
  }
  .card--front { left: 267px; top: 159px; }
  .card--back  { left: 262px; top: 653px; }

  .front-art {
    position: absolute;
    inset: 0;
    width: 100%;
    height: 100%;
  }
  .details {
    position: absolute;
    right: 60px;
    top: 0;
    text-align: right;
    color: var(--text-white);
    font-family: "Arimo", Arial, sans-serif;
  }
  .holder-name {
    position: absolute;
    right: 0;
    top: 56px;
    margin: 0;
    white-space: nowrap;
    font-family: "Montserrat", Arial, sans-serif;
    font-weight: 800;
    font-size: 25px;
    letter-spacing: 0.3px;
  }
  .holder-role {
    position: absolute;
    right: 0;
    top: 90px;
    margin: 0;
    font-size: 16px;
    white-space: nowrap;
  }
  .address {
    position: absolute;
    right: -4px;
    top: 185px;
    margin: 0;
    font-style: normal;
    font-size: 16.5px;
    line-height: 21px;
    white-space: nowrap;
  }
  .contact-list {
    position: absolute;
    right: 0;
    top: 248px;
    margin: 0;
    padding: 0;
    list-style: none;
    font-size: 16.5px;
    line-height: 20.5px;
    white-space: nowrap;
  }
  .contact-list li {
    display: flex;
    justify-content: flex-end;
    align-items: center;
    gap: 10px;
  }
  .contact-icon { width: 14px; height: 14px; flex: none; }
  .website {
    position: absolute;
    right: 0;
    top: 326px;
    margin: 0;
    font-size: 16.5px;
    white-space: nowrap;
  }

  .brand-lockup {
    position: absolute;
    left: 0;
    right: 0;
    top: 170px;
    display: flex;
    justify-content: center;
    align-items: center;
    gap: 14px;
    color: var(--emboss-blue);
    font-family: "Arimo", Arial, sans-serif;
    font-weight: 700;
    font-size: 30px;
    letter-spacing: 2px;
  }
  .brand-mark {
    width: 28px;
    height: 28px;
    background: var(--emboss-blue);
  }
</style>
</head>
<body>
<main class="canvas">
  <section class="card card--front" aria-label="Card front">
    <svg class="front-art" viewBox="0 0 800 458" preserveAspectRatio="none" aria-hidden="true">
      <rect width="800" height="458" fill="var(--card-blue)"/>
      <polygon points="0,0 228,0 122,458 0,458" fill="var(--paper-white)"/>
      <polygon points="228,0 373,0 126,458 122,458" fill="var(--accent-red)" stroke="var(--paper-white)" stroke-width="2"/>
    </svg>
    <div class="details">
      <h1 class="holder-name">DANIEL HARPER</h1>
      <p class="holder-role">President</p>
      <address class="address">2418 Ridgeview Road<br>Hobart, Canada 70213</address>
      <ul class="contact-list">
        <li>512-880-4107
          <svg class="contact-icon" viewBox="0 0 16 16" aria-hidden="true"><path d="M3 1l3 3-2 2c1 2 3 4 5 5l2-2 3 3-2 3C6 14 2 10 1 3z" fill="var(--accent-red)"/></svg>
        </li>
        <li>512-339-7261
          <svg class="contact-icon" viewBox="0 0 16 16" aria-hidden="true"><rect x="4" y="1" width="8" height="14" rx="1.5" fill="none" stroke="var(--accent-red)" stroke-width="1.8"/></svg>
        </li>
        <li>info@KVE.com
          <svg class="contact-icon" viewBox="0 0 16 16" aria-hidden="true"><rect x="1" y="3" width="14" height="10" fill="var(--accent-red)"/><path d="M1 3l7 6 7-6" fill="none" stroke="var(--card-blue)" stroke-width="1.2"/></svg>
        </li>
      </ul>
      <p class="website">www.KVE.com</p>
    </div>
  </section>

  <section class="card card--back" aria-label="Card back">
    <div class="brand-lockup">
      <span class="brand-mark" aria-hidden="true"></span>
      <span class="brand-name">KEYSTONE VOLT ELECTRICAL</span>
    </div>
  </section>
</main>
</body>
</html>
```